Brochure and Business Card design

I am looking for a high end, elegant A4, 4 page brochure booklet to convey our products to clientele that will be visiting a luxury display showroom.

Corvelle Security is a Australian security provider, and we supply high end products from reputable brands.
The brochure will be directed to clients building a new home with a partnered building company and will be accompanied with display boards of our products.

I am providing files of a document we have put together with the relevant information and some images to help along the way, we are not bound by the layout or style it has been drawn up and we wish to give you complete creative freedom putting the peaces together. I have also provided the files for our logo in two different colours, and a picture of a brochure we love the look of.

If you have any suggestions, we can likely come up with further images etc if it will help or even if you feel some should be removed, we are open to that also

Target Market(s)

Young familys, people building new luxury homes, proffesionals, home owners

Industry/Entity Type

Business

Font styles to use
Serif
Sans Serif

Requirements
Must have
• All 8 pages
Should not have
• Not really a fan of reds and similar.

```html
<!DOCTYPE html>
<html lang="en">
<head>
<meta charset="utf-8">
<title>Corvelle Security – Alarm Systems &amp; Intercom</title>
<link href="https://fonts.googleapis.com/css2?family=Didact+Gothic&family=Montserrat:wght@600;700&display=swap" rel="stylesheet">
<style>
:root{
  --stage:#cfcfcf;
  --paper:#ffffff;
  --blue:#2585c8;
  --blue-deep:#1f78bd;
  --green:#7fbf2a;
  --lime:#c9d629;
  --text:#4a4a4a;
  --label:#3a3a3a;
  --rule:#bdbdbd;
  --box-line:#e8e8e8;
}
*{margin:0;padding:0;box-sizing:border-box}
html,body{width:1200px;height:645px;overflow:hidden;background:var(--stage)}
body{position:relative;font-family:"Didact Gothic",sans-serif;color:var(--text)}
.page-label{position:absolute;top:98px;font:700 11px "Montserrat",sans-serif;color:#111}
.page-label.left{left:328px}
.page-label.right{left:846px}
.spread{position:absolute;left:98px;top:127px;width:1002px;height:388px;background:var(--paper);overflow:hidden}
.waves,.ring-accent{position:absolute;left:0;top:0}
.photo-ring{position:absolute;width:150px;height:150px;border-radius:50%;border:5px solid #fff;box-shadow:0 0 0 1px #e2e2e2}
.photo-ring.alarm{left:39px;top:12px;background:linear-gradient(100deg,#e6eaec 0 22%,#3a3a3a 34% 72%,#d8dbdc 82%)}
.photo-ring.intercom{left:822px;top:12px;background:linear-gradient(160deg,#f1eee9,#cfc6b8)}
.title{position:absolute;font-weight:400;color:var(--blue-deep);line-height:1}
.title.alarm{left:285px;top:74px;font-size:28px}
.title.intercom{left:514px;top:58px;font-size:30px}
.body-copy{position:absolute;font-size:6.9px;line-height:7.6px;text-align:justify}
.body-copy p+p{margin-top:7.6px}
.alarm-copy{left:286px;top:110px;width:187px}
.intercom-copy{left:515px;top:94px;width:289px}
.kits-copy{left:14px;top:196px;width:248px;line-height:7.9px}
.section-head{position:absolute;font:700 10px "Montserrat",sans-serif;color:var(--green);letter-spacing:.2px}
.upgrade{position:absolute;width:107px;height:47px;border:1px solid var(--box-line);display:flex;align-items:center;gap:6px;padding:4px}
.upgrade .thumb{width:38px;height:37px;flex:none;background:linear-gradient(135deg,#fafafa,#cfcfcf)}
.upgrade span{font:600 5.8px/7.2px "Montserrat",sans-serif;color:var(--label)}
.upgrade.wide{width:146px;height:50px;padding:5px;gap:10px}
.upgrade.wide .thumb{width:48px;height:38px}
.product-thumb{position:absolute;width:73px;height:45px;background:linear-gradient(135deg,#f0ede6,#b7a98d)}
.product-thumb.grey{background:linear-gradient(135deg,#eeeeee,#8e8e8e)}
.product-name{position:absolute;left:600px;font:600 9.6px "Montserrat",sans-serif;color:var(--blue-deep)}
.product-copy{position:absolute;left:600px;width:204px;font-size:6.4px;line-height:7.1px;text-align:justify}
.rule{position:absolute;left:515px;width:289px;height:1px;background:var(--rule)}
</style>
</head>
<body>
<div class="page-label left">Page 2</div>
<div class="page-label right">Page 3</div>

<main class="spread">
  <svg class="waves" width="1002" height="170" viewBox="0 0 1002 170">
    <g id="left-swoosh">
      <path d="M-10 85C30 84 70 79 120 70C200 55 300 30 400 24C340 34 280 52 200 74C130 94 60 112 -10 122Z" fill="var(--green)"/>
      <path d="M-10 125C80 119 200 93 300 58" stroke="var(--lime)" stroke-width="3" fill="none"/>
    </g>
    <g transform="translate(1002 0) scale(-1 1)">
      <path d="M-10 85C30 84 70 79 120 70C200 55 300 30 400 24C340 34 280 52 200 74C130 94 60 112 -10 122Z" fill="var(--green)"/>
      <path d="M-10 125C80 119 200 93 300 58" stroke="var(--lime)" stroke-width="3" fill="none"/>
    </g>
    <path d="M-10 -10H1012V85C972 84 932 79 882 70C802 55 702 30 602 24C562 22 532 30 501 41C470 30 440 22 400 24C300 30 200 55 120 70C70 79 30 84 -10 85Z" fill="var(--blue)" stroke="#fff" stroke-width="8" paint-order="stroke"/>
    <line x1="501" y1="0" x2="501" y2="41" stroke="#e8eef4" stroke-width="1"/>
  </svg>

  <div class="photo-ring alarm" role="img" aria-label="Wall-mounted alarm keypad beside a dark doorway"></div>
  <div class="photo-ring intercom" role="img" aria-label="Video intercom monitor mounted on a wall"></div>
  <svg class="ring-accent" width="1002" height="180" viewBox="0 0 1002 180">
    <path d="M189.2 114.4A80 80 0 0 1 154 156.3" stroke="var(--blue)" stroke-width="4" fill="none"/>
    <path d="M154 156.3A80 80 0 0 1 62.6 148.3" stroke="var(--lime)" stroke-width="4" fill="none"/>
    <path d="M827.7 127A80 80 0 0 0 897 167" stroke="var(--lime)" stroke-width="4" fill="none"/>
    <path d="M972.2 114.4A80 80 0 0 1 942.9 152.5" stroke="var(--blue)" stroke-width="4" fill="none"/>
  </svg>

  <!-- Alarm page -->
  <h1 class="title alarm">Alarm Systems</h1>
  <div class="body-copy alarm-copy">
    <p>A Corvelle Security alarm system with its state of the art equipment is the perfect defense for your family and home. With detection devices such as motion detectors, magnetic door sensors and warning devices like siren + strobe combos to alert others of a break in to name a few, it will be everything you need to feel secure.</p>
    <p>With the added option of having your security system monitored, you will always have someone watching over your home, even when even when the house is vacant..</p>
    <p>Did you know, industry leaders say that burglars are 3 times more likely to target a home without a security system. This means that simply having a home security system always keeps you safer, even if an alarm is never triggered.</p>
  </div>

  <h2 class="section-head" style="left:14px;top:173px">HOME KITS</h2>
  <p class="body-copy kits-copy">Standard kits consisting of everything you need to get an alarm up and running. Components such as an Alarm Control Panel, Keypad, 3 motion detectors, and internal siren, an external siren+strobe combo, battery back up incase the power goes out. A great starting platform that can be built on to your needs and requirements.</p>

  <h2 class="section-head" style="left:14px;top:245px">POPULAR UPGRADES</h2>
  <div class="upgrade" style="left:14px;top:269px"><div class="thumb" role="img" aria-label="OLED keypad"></div><span>OLED Keypad upgrade</span></div>
  <div class="upgrade" style="left:134px;top:269px"><div class="thumb" role="img" aria-label="Remote fobs"></div><span>Remote Arm and Disarm</span></div>
  <div class="upgrade" style="left:251px;top:269px"><div class="thumb" role="img" aria-label="Ceiling motion detector"></div><span>360 degree motion detectors</span></div>
  <div class="upgrade" style="left:371px;top:269px"><div class="thumb" role="img" aria-label="Magnetic reed switch"></div><span>Door and window magnetic switches</span></div>
  <div class="upgrade" style="left:14px;top:324px"><div class="thumb" role="img" aria-label="Monitoring communicator"></div><span>Professional Alarm Monitoring</span></div>
  <div class="upgrade" style="left:134px;top:324px"><div class="thumb" role="img" aria-label="Wall motion detector"></div><span>Motion Detectors' in additional rooms</span></div>
  <div class="upgrade" style="left:251px;top:324px"><div class="thumb" role="img" aria-label="Roller door switch"></div><span>Roller door magnetic switch</span></div>

  <!-- Intercom page -->
  <h1 class="title intercom">Intercom</h1>
  <div class="body-copy intercom-copy">
    <p>A Corvelle Security Intercom system is a great addition to any home. Giving you the ability to communicate with visitors to your home at your front door or even at your front gate. In conjunction with the use of an electric strike you can hit the door release button on the intercom and let them in from where you stand in the home. Maybe even better still, decide to not let them in.</p>
    <p>With the video intercom option your visitor will be displayed automatically and you can view who it is without them even knowing you are there.</p>
  </div>

  <div class="product-thumb" style="left:515px;top:177px" role="img" aria-label="Colour video intercom kit"></div>
  <h3 class="product-name" style="top:174px">HX Colour Video Intercom</h3>
  <p class="product-copy" style="top:187px">Superior quality, touch button control and door release. This sleek glass face 7" screen intercom is just what you need to visually see and communicate with who is at the front gate or door. With the add on addition of a extra monitor makes it perfect for two story homes with the extra station up stairs.</p>
  <div class="rule" style="top:234px"></div>

  <div class="product-thumb grey" style="left:515px;top:257px;height:36px" role="img" aria-label="Glass face video monitor and door station"></div>
  <h3 class="product-name" style="top:245px">HV Colour Video Intercom</h3>
  <p class="product-copy" style="top:258px">All the smarts built into a compact, modern designed glass face monitor. This unit has touch screen control, inter home communication between monitors and a build in handset for minimal disturbance when required. With maximums of 4 door stations and 8 Monitors, this system is perfect for the homes with multiple entry points and where multiple room monitors are required.</p>
  <div class="rule" style="top:316px"></div>

  <div class="product-thumb grey" style="left:532px;top:325px;width:38px;height:44px" role="img" aria-label="Audio door station and handset"></div>
  <h3 class="product-name" style="top:324px">Audio Only Intercom</h3>
  <p class="product-copy" style="top:337px">Whether it's to help fit within the budget, and you just don't have the requirement of having to see who is at the door, this no fuss, single purpose audio only intercom is that handy addition to the living area.</p>

  <h2 class="section-head" style="left:840px;top:179px">POPULAR UPGRADES</h2>
  <div class="upgrade wide" style="left:840px;top:202px"><div class="thumb" role="img" aria-label="Stainless steel door station"></div><span>Upgrade to flush mount stainless steel door station</span></div>
  <div class="upgrade wide" style="left:840px;top:257px"><div class="thumb" role="img" aria-label="Electric strike"></div><span>Extend Intercom wiring to property font gate</span></div>
  <div class="upgrade wide" style="left:840px;top:312px"><div class="thumb" role="img" aria-label="Additional video monitor"></div><span>Additional monitor installed. (Video Only)</span></div>
</main>
</body>
</html>
```